Course Lantern

CourseLantern.example will be a place for people looking for information, resources, and advisement to start or continue their education. We want a friendly, inviting site design that makes finding what potential students are looking for simple and easy to navigate. We are not committed to the colors of the logo, so variations on the color scheme are welcome.

Text instructions based on the wireframe: For the site's homepage we'd like a banner at the very top for our Logo and white space to the right of it. See attachments for logo + wireframe. Below that would be navigation. Below that split into 2/3 on the left we would have home page content, and 1/3 on the right we would have the lead form. At the bottom of the page we would have a space for types of degrees, then a footer with copyright info + site info.

See wireframes for additional page layouts.

Industry/Entity Type

Education

Requirements
Must have
• At minimum we are looking for three pages: homepage, choose your degree path page, and content page.
Nice to have
• -White space is appreciated
-Variations on the color scheme are welcome, we are not married to the existing logo's color scheme.

```html
<!DOCTYPE html>
<html lang="en">
<head>
<meta charset="utf-8">
<title>Course Lantern</title>
<link href="https://fonts.googleapis.com/css2?family=Ubuntu:wght@400;500;700&family=Arimo:wght@400;700&display=swap" rel="stylesheet">
<style>
:root{
  --orange:#e8461a;
  --ink:#4a4a4a;
  --body:#4d4d4d;
  --cream:#f1efe3;
  --field:#c9c4b3;
  --nav:#1e1e1e;
  --teal:#2b5e6b;
  --footer:#3a3a3a;
}
*{margin:0;padding:0;box-sizing:border-box}
html,body{width:932px;height:1200px;overflow:hidden}
body{position:relative;background:var(--cream);font-family:Arimo,Arial,sans-serif;color:var(--body)}
.abs{position:absolute}
.backdrop{left:0;top:93px;width:932px;height:440px;
  background:linear-gradient(90deg,#e06a3a 0%,#f0b35a 4%,#e9d3a8 7%,rgba(241,239,227,0) 10%,rgba(241,239,227,0) 90%,#f0b0a8 94%,#d8506a 100%),
  linear-gradient(180deg,#f3c9a0 0%,#f2e6d0 40%,var(--cream) 100%)}
.header{left:0;top:0;width:932px;height:93px;background:linear-gradient(#fff,#f1f1f1)}
.column{left:61px;top:144px;width:810px;height:964px;background:var(--cream);border-left:1px solid #fff;border-right:1px solid #fff}
.brand{left:79px;top:32px;font-family:Ubuntu,sans-serif;font-weight:500;font-size:30px;color:#555;display:flex;align-items:center;gap:8px;letter-spacing:-.5px}
.brand i{display:block;width:14px;height:14px;background:var(--orange)}
.follow{left:724px;top:11px;font-size:8.5px;font-weight:700;color:#666;display:flex;align-items:center;gap:5px}
.follow span.sq{width:15px;height:15px;background:#555;border-radius:2px;display:inline-block}
.follow b{margin-right:6px;font-weight:700}
.callicon{left:685px;top:36px;width:47px;height:47px;border-radius:6px;background:linear-gradient(#f58a3a,#e2531c);box-shadow:0 0 0 3px #f3f3f3,0 1px 4px rgba(0,0,0,.3)}
.tollfree{left:739px;top:45px;font-family:Ubuntu,sans-serif;font-size:12px;color:var(--teal)}
.tollnum{left:739px;top:58px;font-family:Ubuntu,sans-serif;font-weight:700;font-size:17px;color:var(--teal);letter-spacing:.3px}
.nav{left:49px;top:105px;width:834px;height:39px;background:var(--nav)}
.nav-end{top:115px;width:22px;height:40px;background:#222}
.nav-end.l{left:27px;clip-path:polygon(0 0,100% 0,100% 100%,0 100%,35% 50%)}
.nav-end.r{left:883px;clip-path:polygon(0 0,100% 0,65% 50%,100% 100%,0 100%)}
.tab{left:297px;top:96px;width:81px;height:42px;background:linear-gradient(#fff,#efefef);border-top:3px solid #ddd}
.navlink{top:116px;font-family:Ubuntu,sans-serif;font-size:11.3px;color:#eee;letter-spacing:.5px}
.navlink.home{color:#333}
.sep{top:110px;height:28px;border-left:1px dashed #555}
.slider{left:72px;top:151px;width:786px;height:321px;background:#f2f2f2;border:1px solid #ddd;box-shadow:0 1px 3px rgba(0,0,0,.15)}
.photo{left:81px;top:160px;width:769px;height:283px;background:linear-gradient(90deg,#3b4452 0%,#8a8a86 30%,#c6bcb0 45%,#2b3040 55%,#e4d4c8 75%,#f2f2f2 100%)}
.dot{top:451px;width:13px;height:13px;border-radius:50%;background:#aaa}
.dot.on{background:#333}
.shelf{left:82px;top:472px;width:768px;height:24px;background:radial-gradient(ellipse at 50% 0,#d8d4c6 0%,rgba(241,239,227,0) 70%)}
.art{background:#8a8a8a}
h1.welcome{left:143px;top:521px;font-family:Ubuntu,sans-serif;font-weight:500;font-size:26px;color:#555;white-space:nowrap}
h1 em,h2 em{font-style:normal;color:var(--orange)}
.rule{height:3px;background:linear-gradient(90deg,#c9c5b8,rgba(201,197,184,0))}
.copy{font-size:10.2px;line-height:14.6px;text-align:justify;width:479px;left:88px}
.copy p+p{margin-top:14.6px}
.btn{background:#2a2a2a;color:#fff;font-size:9.3px;border-radius:3px;display:flex;align-items:center;justify-content:center;gap:3px}
h2{font-family:Ubuntu,sans-serif;font-weight:500;color:#555;white-space:nowrap}
.divider{left:592px;top:509px;height:434px;border-left:1px solid #cfcbbd}
.lead-intro{left:615px;top:555px;width:211px;font-size:10.2px;line-height:13.6px;text-align:justify;color:#666}
.field{left:614px;width:217px;height:21px;background:var(--field);border:1px solid #dedbd0;font-size:10.2px;color:#444;padding:5px 6px}
.field .arrow{position:absolute;right:0;top:0;width:22px;height:19px;border-left:1px solid #ddd}
.field .arrow::after{content:"";position:absolute;left:7px;top:7px;border:4px solid transparent;border-top-color:#333}
.or{left:709px;top:781px;font-family:Ubuntu,sans-serif;font-weight:700;font-size:35px;color:#d6d3c8}
.callbox{left:608px;top:827px;width:238px;height:110px;background:#fff;border:1px solid #e2e2e2}
.handset{left:609px;top:828px;width:80px;height:108px;background:linear-gradient(135deg,#f4f4f4,#e89a6a 60%,#f4f4f4)}
.click{left:698px;top:828px;font-family:Ubuntu,sans-serif;font-weight:700;font-size:39px;color:var(--orange);letter-spacing:1px}
.callnow{left:704px;top:867px;font-family:Ubuntu,sans-serif;font-weight:700;font-size:14px;color:#222;letter-spacing:1px}
.callsmall{left:689px;top:886px;font-size:8.8px;line-height:13px;color:#222}
.callnum{left:689px;top:913px;font-family:Ubuntu,sans-serif;font-weight:700;font-size:18.5px;color:#333;letter-spacing:.5px}
.degrees{left:82px;top:981px;width:767px;height:107px;background:#fff;border-radius:5px;box-shadow:0 0 3px rgba(0,0,0,.2)}
.degrees-inner{left:88px;top:986px;width:755px;height:97px;background:#ececec;border-radius:4px}
.cert{top:995px;width:97px;height:73px;border:3px solid}
.footer{left:0;top:1108px;width:932px;height:92px;background:var(--footer)}
.foot-brand{left:73px;top:1146px;font-family:Ubuntu,sans-serif;font-weight:500;font-size:23px;color:#d0d0d0;display:flex;align-items:center;gap:7px}
.foot-brand i{display:block;width:12px;height:12px;background:#bbb}
.foot-links{left:301px;top:1139px;font-size:10px;color:#c8c8c8;word-spacing:2px}
.foot-copy{left:295px;top:1156px;font-size:10px;color:#c8c8c8}
.address{right:75px;top:1123px;text-align:right;font-size:10px;line-height:16.2px;color:#aaa}
.address b{font-weight:700}
</style>
</head>
<body>
<div class="abs backdrop" role="img" aria-label="Soft abstract background of flowing warm colour ribbons"></div>
<div class="abs header"></div>
<div class="abs column"></div>

<div class="abs brand"><span>Course Lantern</span><i></i></div>
<div class="abs follow"><b>Follow Us on :</b><span class="sq" aria-label="Social link"></span><span class="sq" aria-label="Social link"></span><span class="sq" aria-label="Social link"></span></div>
<div class="abs callicon">
  <svg width="47" height="47" viewBox="0 0 47 47"><rect x="14" y="12" width="19" height="23" rx="3" fill="none" stroke="#fff" stroke-width="2"/><rect x="24" y="15" width="6" height="17" rx="1" fill="#fff"/><g fill="#fff"><rect x="17" y="16" width="2.5" height="2.5"/><rect x="17" y="21" width="2.5" height="2.5"/><rect x="17" y="26" width="2.5" height="2.5"/></g></svg>
</div>
<div class="abs tollfree">CALL US TOLL-FREE</div>
<div class="abs tollnum">555 .014 .2086</div>

<div class="abs nav-end l"></div>
<div class="abs nav-end r"></div>
<nav class="abs nav"></nav>
<div class="abs tab"></div>
<span class="abs navlink home" style="left:322px">HOME</span>
<span class="abs navlink" style="left:401px">ABOUT US</span>
<span class="abs sep" style="left:475px"></span>
<span class="abs navlink" style="left:496px">SERVICES</span>
<span class="abs sep" style="left:569px"></span>
<span class="abs navlink" style="left:590px">DEGREES</span>
<span class="abs sep" style="left:662px"></span>
<span class="abs navlink" style="left:687px">FAQ'S</span>
<span class="abs sep" style="left:745px"></span>
<span class="abs navlink" style="left:763px">CONTACT US</span>

<div class="abs slider"></div>
<div class="abs photo" role="img" aria-label="Photo of a smiling graduate in cap and gown with classmates behind"></div>
<span class="abs dot on" style="left:425px"></span>
<span class="abs dot" style="left:446px"></span>
<span class="abs dot" style="left:467px"></span>
<span class="abs dot" style="left:488px"></span>
<span class="abs dot" style="left:509px"></span>
<div class="abs shelf"></div>

<div class="abs art" style="left:94px;top:510px;width:38px;height:51px;border-radius:6px" role="img" aria-label="Welcome tag illustration"></div>
<h1 class="abs welcome">Welcome - <em>Course Lantern</em></h1>
<div class="abs rule" style="left:143px;top:559px;width:330px"></div>
<div class="abs copy" style="top:573px">
  <p>Curabitur mattis sem tincidunt arcu gravida aliquet. In hac habitasse platea dictumst. Class aptent taciti sociosqu ad litora torquent per conubia nostra, per inceptos himenaeos. Quisque nisi risus, varius et sodales vitae, imperdiet vel sapien. In et est a elit luctus lacinia eu vel sapien. Mauris pulvinar venenatis elit nec egestas.</p>
  <p>Proin hendrerit euismod velit, non imperdiet dolor aliquam et. Nullam id nulla vitae sem congue ultrices eu id sapien. Donec et dolor ac dui suscipit pellentesque. Pellentesque habitant morbi tristique senectus et netus et malesuada fames ac turpis egestas. Nunc at velit sapien. Aenean iaculis odio quis lacus bibendum volutpat lobortis libero tincidunt. Nullam ut risus turpis. In nulla tellus, semper ut ornare et, adipiscing sed arcu.</p>
</div>
<div class="abs btn" style="left:507px;top:724px;width:60px;height:18px">Read more <span style="font-size:6px">&#9654;</span></div>

<div class="abs art" style="left:92px;top:766px;width:34px;height:47px;border-radius:40% 40% 10% 10%;background:#9a9a9a" role="img" aria-label="Illustration of a figure beside a question mark"></div>
<h2 class="abs" style="left:130px;top:778px;font-size:14.6px">Why <em>Course Lantern ??</em></h2>
<div class="abs rule" style="left:131px;top:804px;width:160px"></div>
<div class="abs copy" style="top:821px">
  <p>Pellentesque habitant morbi tristique senectus et netus et malesuada fames ac turpis egestas. Nunc at velit sapien. Aenean iaculis odio quis lacus bibendum volutpat lobortis libero tincidunt. Nullam ut risus turpis. In nulla tellus, semper ut ornare et, adipiscing sed arcu.<br>Quisque nisi risus, varius et sodales vitae, imperdiet vel sapien. In et est a elit luctus lacinia eu vel sapien. Mauris pulvinar venenatis elit nec egestas.</p>
</div>
<div class="abs btn" style="left:507px;top:907px;width:60px;height:18px">Read more <span style="font-size:6px">&#9654;</span></div>

<div class="abs divider"></div>

<div class="abs art" style="left:612px;top:509px;width:38px;height:40px;border-radius:8px;background:#a5a5a5" role="img" aria-label="Illustration of a figure at a laptop"></div>
<h2 class="abs" style="left:658px;top:516px;font-size:15.4px">Lead <em>Form</em></h2>
<div class="abs rule" style="left:658px;top:536px;width:95px"></div>
<p class="abs lead-intro">Send us a quick email with any questions or concerns you may have about your potential case.</p>
<div class="abs field" style="top:600px">Your Name</div>
<div class="abs field" style="top:628px">Your Email Address</div>
<div class="abs field" style="top:656px">Your Phone No.</div>
<div class="abs field" style="top:682px">Interested In<span class="arrow"></span></div>
<div class="abs field" style="top:710px;height:60px;padding-top:7px">Provide Your Education Details.</div>
<div class="abs btn" style="left:614px;top:783px;width:61px;height:20px;font-weight:700;font-size:10px;background:linear-gradient(#3a3a3a,#111)">Submit</div>
<div class="abs or">OR</div>

<div class="abs callbox"></div>
<div class="abs handset" role="img" aria-label="Photo of a hand holding an orange telephone handset"></div>
<div class="abs click">CLICK</div>
<div class="abs callnow">CALL-US-NOW</div>
<div class="abs callsmall">Have a question about your career ?<br>Click here to connect to our office.</div>
<div class="abs callnum">555 .014 .2086</div>

<h2 class="abs" style="left:122px;top:948px;font-size:14.6px">List of <em>degrees</em></h2>
<div class="abs rule" style="left:122px;top:971px;width:100px"></div>
<div class="abs degrees"></div>
<div class="abs degrees-inner"></div>
<div class="abs cert" style="left:100px;border-color:#6b2e3c;background:#efe6d8" role="img" aria-label="Degree certificate"></div>
<div class="abs cert" style="left:221px;border-color:#efe7cf;background:#fbf6e8" role="img" aria-label="Degree certificate"></div>
<div class="abs cert" style="left:344px;border-color:#8aa4d8;background:#fbfbfb" role="img" aria-label="Degree certificate"></div>
<div class="abs cert" style="left:467px;border-color:#d2a77a;background:#fbfaf6" role="img" aria-label="Degree certificate"></div>
<div class="abs cert" style="left:593px;border-color:#555;background:#e8e6e0" role="img" aria-label="Degree certificate"></div>
<div class="abs cert" style="left:718px;border-color:#b8b8b8;background:#fafafa" role="img" aria-label="Degree certificate"></div>

<footer class="abs footer"></footer>
<div class="abs foot-brand"><span>Course Lantern</span><i></i></div>
<div class="abs foot-links">Home &nbsp;&nbsp;| &nbsp;&nbsp;About Us &nbsp;&nbsp;| &nbsp;&nbsp;Services &nbsp;&nbsp;| &nbsp;&nbsp;Degrees &nbsp;&nbsp;| &nbsp;&nbsp;FAQs &nbsp;&nbsp;| &nbsp;&nbsp;Contact</div>
<div class="abs foot-copy">Copyright © 2011 - CourseLantern.example - All rights reserved. Terms and Privacy Policy</div>
<div class="abs address"><b>Address Line 1 with City</b><br><b>Address Line 2 with Country</b><br>Tel. : 555 . 014 . 2086<br>Email : info@courselantern.example</div>
</body>
</html>
```